LEARN Business Skills so you can Earn a good living

size of the poster is 8”x 10.75" plus 0.25" bleed.
Please leave 1 inch on the bottoum for footer
I want a design a poster that will attract people's attention.
I appreciate a creative ad however the ad should not take away from being able to clearly read the text.
-I also appreciate a simple creative ad that is not too busy.
-you can use graphics, vectors, or pictures of real people.
-however, if you use real people it should be a white male that is wearing a white shirt and look like a professional person.

Target Market(s)

Potential young business people

Industry/Entity Type

education

Requirements
Must have
• easy to read the text
Nice to have
• I would like a "creative" simple ad that is easy to be read
Should not have
• pictures of women

```html
<!DOCTYPE html>
<html lang="en">
<head>
<meta charset="utf-8">
<title>Business Enrichment Course</title>
<link rel="stylesheet" href="https://fonts.googleapis.com/css2?family=Bebas+Neue&family=Roboto+Condensed:wght@400;700&family=Roboto:wght@400;500;700&display=swap">
<style>
  :root {
    --page-bg: #e4e4e4;
    --navy-deep: #15306a;
    --navy-mid: #1c4389;
    --navy-glow: #2460b3;
    --sky: #22a8e0;
    --pale-blue: #8db6e4;
    --white: #ffffff;
    --icon-ring: #6fa6e0;
    --coin: #e9a93a;
  }
  * { box-sizing: border-box; margin: 0; padding: 0; }
  html, body {
    width: 976px; height: 1200px; overflow: hidden;
    background: var(--page-bg);
  }
  .poster {
    position: absolute; left: 43px; top: 0;
    width: 890px; height: 1200px; overflow: hidden;
    background: radial-gradient(ellipse 70% 55% at 55% 48%, var(--navy-glow) 0%, var(--navy-mid) 45%, var(--navy-deep) 100%);
    color: var(--white);
    font-family: "Roboto", Arial, sans-serif;
  }
  .tagline-band {
    position: absolute; left: 0; top: 34px;
    width: 848px; height: 51px;
    background: var(--sky);
    display: flex; align-items: center; justify-content: center;
    font-family: "Roboto Condensed", "Arial Narrow", sans-serif;
    font-size: 29px; letter-spacing: 0.5px; text-transform: uppercase;
  }
  .tagline-band strong { font-weight: 700; }
  .title {
    position: absolute; left: 0; top: 122px; width: 100%;
    text-align: center; font-weight: 700;
    font-size: 64px; line-height: 70px; letter-spacing: 1px;
  }
  .subtitle {
    position: absolute; left: 0; top: 286px; width: 100%;
    text-align: center; font-size: 21px;
  }
  .hero-art {
    position: absolute; left: 364px; top: 325px;
    width: 500px; height: 460px;
    background: radial-gradient(circle at 60% 45%, #5d8fd6 0%, #2f64b3 45%, rgba(36,96,179,0) 75%);
    border-radius: 40px;
  }
  .slogan {
    position: absolute; left: 40px; top: 408px; width: 330px;
    text-align: center; color: var(--pale-blue);
    font-family: "Roboto", Arial, sans-serif; font-weight: 500;
  }
  .slogan-line { font-size: 82px; line-height: 88px; letter-spacing: 1px; }
  .slogan-to {
    display: flex; align-items: center; justify-content: center; gap: 14px;
    font-size: 40px; height: 60px; color: var(--white);
  }
  .slogan-to .rule {
    position: relative; width: 84px; height: 2px; background: var(--white);
  }
  .slogan-to .rule::before, .slogan-to .rule::after {
    content: ""; position: absolute; top: -4px; width: 10px; height: 10px;
    border-radius: 50%; background: var(--white);
  }
  .slogan-to .rule::before { left: -4px; }
  .slogan-to .rule::after { right: -4px; }
  .benefits-band {
    position: absolute; left: 0; top: 738px;
    width: 390px; height: 48px;
    background: var(--sky);
    clip-path: polygon(0 0, 100% 0, 94% 100%, 0 100%);
    display: flex; align-items: center; padding-left: 40px;
    font-family: "Bebas Neue", "Arial Narrow", sans-serif;
    font-size: 27px; letter-spacing: 0.3px;
  }
  .benefits {
    position: absolute; top: 820px; left: 128px;
    display: flex; gap: 0;
  }
  .benefit { width: 210px; text-align: center; }
  .benefit-icon {
    width: 100px; height: 100px; margin: 0 auto 18px;
    border: 2px dotted var(--icon-ring); border-radius: 50%;
    display: flex; align-items: center; justify-content: center;
  }
  .benefit-label { font-size: 23px; line-height: 30px; }
  .topics {
    position: absolute; left: 60px; top: 1024px; width: 770px;
    text-align: center;
    font-family: "Bebas Neue", "Arial Narrow", sans-serif;
    font-size: 17px; line-height: 22px; letter-spacing: 0.2px;
  }
  .topics b { font-weight: 400; color: var(--white); }
</style>
</head>
<body>
<main class="poster">
  <div class="tagline-band"><span><strong>Learn</strong> business <strong>skills</strong> so you can <strong>earn</strong> a good living</span></div>

  <h1 class="title">BUSINESS<br>ENRICHMENT COURSE</h1>
  <p class="subtitle">A proven success of helping people in their livelihoods</p>

  <div class="hero-art" role="img" aria-label="Illustration of a businessman with a megaphone, gears, a question mark, coin stacks and cheering young professionals"></div>

  <div class="slogan">
    <div class="slogan-line">LEARN IT</div>
    <div class="slogan-to"><span class="rule"></span>to<span class="rule"></span></div>
    <div class="slogan-line">EARN IT</div>
  </div>

  <div class="benefits-band">Business skills that will help you:</div>

  <div class="benefits">
    <div class="benefit">
      <div class="benefit-icon">
        <svg width="58" height="58" viewBox="0 0 58 58" fill="none" stroke="#fff" stroke-width="2.4" stroke-linecap="round" stroke-linejoin="round">
          <circle cx="29" cy="16" r="10"/>
          <path d="M29 10v12M32 12.5c-1-1.2-5-1.5-5 .8 0 2.6 5 1.4 5 4 0 2.2-4 2-5.3.6"/>
          <path d="M6 44c8-6 14-7 22-4h10c3 0 3 4 0 4H27M38 42l10-6c3-2 5 1 3 3l-13 9c-4 2-14 2-24-1"/>
        </svg>
      </div>
      <p class="benefit-label">Get a<br>quality job</p>
    </div>
    <div class="benefit">
      <div class="benefit-icon">
        <svg width="58" height="58" viewBox="0 0 58 58" fill="none" stroke="#fff" stroke-width="2.4" stroke-linecap="round" stroke-linejoin="round">
          <path d="M14 24l8-8 6 5 12-12M34 9h6v6"/>
          <path d="M24 48V34M32 46V28M40 46V22M48 46V16" stroke-width="4"/>
          <circle cx="16" cy="38" r="7"/>
          <path d="M21 43l7 7"/>
        </svg>
      </div>
      <p class="benefit-label">Start/grow<br>your business</p>
    </div>
    <div class="benefit">
      <div class="benefit-icon">
        <svg width="58" height="58" viewBox="0 0 58 58" fill="none" stroke="#fff" stroke-width="2.4" stroke-linecap="round" stroke-linejoin="round">
          <rect x="12" y="16" width="36" height="22" rx="2" transform="rotate(-10 30 27)"/>
          <rect x="8" y="24" width="38" height="22" rx="2"/>
          <circle cx="27" cy="35" r="6"/>
          <path d="M27 31v8"/>
          <path d="M4 48c4 2 8 2 12 0"/>
        </svg>
      </div>
      <p class="benefit-label">Increase<br>your salary</p>
    </div>
  </div>

  <p class="topics">Business administration - <b>small business management</b> - finance - <b>investments</b> - computers- <b>accounting</b> - sales marketing - <b>project management</b> interviewing skills - business law - <b>negotiation</b> – public speaking - <b>import/export</b> - <b>information technoloy</b> - <b>distribution</b> marketing - <b>LedgerBooks</b> - real estate - <b>health care</b> - management - <b>ShopStream</b></p>
</main>
</body>
</html>
```